Logo & nopcommerce theme design for a webshop in gadgets & lifestyle products

We are looking for someone who can design a logo and a nopcommerce theme for our webshop. The name of the shop is Lumavorp. The logo should also be used for plaztrove. In the attached file we have an example of a theme that is close what we are looking for. The coloring should be different but the lay-out is ok. Only on the left we want a column to choose a sub category and a column where you can set some filters to search in detail for a product.

Industry/Entity Type

Shop

Number of Pages Required

1 page

Requirements
Must have
• The Nopcommerce theme for 3.40 should have a professional look, not to color full and for the rest we leave it to the designer
Nice to have
• n/a
Should not have
• n/a

```html
<!DOCTYPE html>
<html lang="en">
<head>
<meta charset="utf-8">
<title>Lumavorp – Smartphones &amp; Mobile Phones</title>
<link href="https://fonts.googleapis.com/css2?family=Open+Sans:wght@400;600;700;800&display=swap" rel="stylesheet">
<style>
:root{
  --red:#d6503f;
  --dark:#3a3d42;
  --darker:#2f3236;
  --bg:#f1f1f1;
  --panel:#ffffff;
  --line:#dcdcdc;
  --side:#ececec;
  --text:#333639;
  --muted:#6b6e72;
  --foot-text:#d9dadb;
}
*{box-sizing:border-box;margin:0;padding:0}
html,body{width:1200px;height:2769px;overflow:hidden}
body{background:var(--bg);font-family:"Open Sans",Arial,sans-serif;color:var(--text);position:relative}
.topline{position:absolute;top:0;left:0;width:1200px;height:5px;background:var(--dark)}
.logo{position:absolute;left:183px;top:22px;font-size:34px;font-weight:700;color:var(--dark);letter-spacing:-.5px}
.utility{position:absolute;left:558px;top:26px;font-size:11px;color:var(--text);display:flex;align-items:center;gap:6px}
.utility b{font-weight:700}
.utility svg{width:14px;height:14px}
.lang,.currency{position:absolute;top:18px;display:flex;gap:2px}
.lang{left:807px}.currency{left:894px}
.lang span,.currency span{display:block;width:22px;height:34px;line-height:34px;text-align:center;font-size:10px;background:#dedede;color:var(--text)}
.lang span.on,.currency span.on{background:var(--dark);color:#fff}
.cart{position:absolute;left:960px;top:18px;width:59px;height:34px;background:var(--dark);display:flex;align-items:center;justify-content:center}
.navbar{position:absolute;top:65px;left:0;width:1200px;height:33px;background:var(--dark)}
.nav{position:absolute;left:183px;top:0;display:flex;height:33px}
.nav a{color:#fff;font-size:12px;text-decoration:none;line-height:33px;padding:0 17px}
.nav a.on{background:var(--red)}
.search{position:absolute;left:788px;top:5px;width:231px;height:23px;background:#fff;font-size:10px;color:var(--text);line-height:23px;padding-left:8px}
.search svg{position:absolute;right:7px;top:5px}
.catbar{position:absolute;left:183px;top:124px;width:280px;height:33px;background:var(--red);color:#fff;font-size:16px;line-height:33px;padding-left:24px}
.catbar svg{position:absolute;right:18px;top:12px}
.crumbs{position:absolute;left:476px;top:124px;width:543px;height:33px;background:#e9e9e9;border:1px solid var(--line);font-size:11px;line-height:31px;padding-left:14px;color:var(--text)}
.crumbs i{font-style:normal;margin:0 22px;font-weight:700}
.tab{position:absolute;top:186px;height:35px;font-size:12px;text-align:center;line-height:34px;border:1px solid var(--line);border-bottom:none}
.tab.all{left:183px;width:173px;background:#e2e2e2}
.tab.offers{left:364px;width:171px;background:#fff;z-index:2;height:36px}
.panel{position:absolute;left:183px;top:220px;width:836px;height:2198px;background:var(--panel);border:1px solid var(--line)}
.panel h1{position:absolute;left:14px;top:12px;font-size:16px;font-weight:400;word-spacing:8px}
.panel .rule{position:absolute;left:14px;right:14px;top:46px;border-top:1px solid var(--line)}
.filters{position:absolute;left:15px;top:68px;width:173px;height:1036px;background:var(--side);padding-top:4px}
.filters h2{font-size:16px;font-weight:400;padding:0 10px;height:32px;line-height:32px;border-bottom:1px solid #d3d3d3;margin-bottom:8px;margin-top:8px}
.filters h2:first-child{margin-top:0}
.filters ul{list-style:none;background:#fff;margin:0 0 0 0;padding:0 0 4px}
.filters li{font-size:10px;height:30px;line-height:30px;padding-left:36px;position:relative;background:var(--side)}
.filters li::before{content:"";position:absolute;left:12px;top:11px;width:9px;height:9px;border:1px solid #bbb;background:#fff}
.grid{position:absolute;left:200px;top:68px;display:grid;grid-template-columns:303px 303px;column-gap:13px;row-gap:15px}
.card{position:relative;height:403px;border:1px solid var(--line);background:#fff;text-align:center;overflow:hidden}
.ribbon{position:absolute;left:0;top:0;width:52px;height:52px}
.shot{position:absolute;left:96px;top:24px;width:110px;height:150px;border-radius:40px;background:radial-gradient(circle at 50% 45%,#e9ebea 0,#b9bcbc 38%,#8d9090 62%,#d2d3d3 100%)}
.card h3{position:absolute;top:186px;left:0;right:0;font-size:11px;font-weight:700}
.card ul{position:absolute;top:214px;left:0;right:0;list-style:none;font-size:10px;line-height:15px}
.card li::before{content:"• "}
.price{position:absolute;top:290px;left:0;right:0;color:var(--red);font-size:24px;font-weight:700}
.price small{font-size:10px;color:var(--text);font-weight:400;margin-left:4px}
.btn{position:absolute;top:336px;left:92px;width:118px;height:30px;background:var(--red);color:#fff;font-size:10px;font-weight:700;line-height:30px}
.footer{position:absolute;top:2463px;left:0;width:1200px;height:236px;background:var(--dark);color:var(--foot-text)}
.fcol{position:absolute;top:30px;width:188px}
.fcol h4{font-size:16px;font-weight:400;color:#fff;padding-bottom:8px;border-bottom:1px solid #55585d;margin-bottom:20px}
.fcol p{font-size:10px;height:28px;display:flex;align-items:center;gap:10px}
.bottom{position:absolute;top:2699px;left:0;width:1200px;height:70px;font-size:10px;color:var(--text)}
.bottom .copy{position:absolute;left:183px;top:29px}
.bottom .social{position:absolute;left:560px;top:24px;font-size:13px;font-weight:700;color:var(--dark);display:flex;gap:14px}
</style>
</head>
<body>
<div class="topline"></div>
<div class="logo">Lumavorp</div>
<div class="utility">
  <svg viewBox="0 0 14 14"><path d="M3 1h3l1 3-2 1a8 8 0 0 0 4 4l1-2 3 1v3c0 1-1 2-2 2A11 11 0 0 1 1 3c0-1 1-2 2-2z" fill="#333639"/></svg>
  <span><b>Call us:</b> (0000) 000 0000 &nbsp;•&nbsp; Signup &nbsp;•&nbsp; Sign in &nbsp;•</span>
</div>
<div class="lang"><span class="on">EN</span><span>FR</span><span>GM</span></div>
<div class="currency"><span class="on">$</span><span>€</span><span>£</span></div>
<div class="cart"><svg width="18" height="16" viewBox="0 0 18 16"><path d="M1 1h3l2 9h9l2-6H5" fill="none" stroke="#d6503f" stroke-width="1.6"/><circle cx="7" cy="13.5" r="1.4" fill="#d6503f"/><circle cx="14" cy="13.5" r="1.4" fill="#d6503f"/></svg></div>

<div class="navbar">
  <nav class="nav"><a>Home</a><a class="on">Products</a><a>Register</a><a>Shop</a></nav>
  <div class="search">Search entire store here...
    <svg width="13" height="13" viewBox="0 0 13 13"><circle cx="5.5" cy="5.5" r="4" fill="none" stroke="#333" stroke-width="1.6"/><path d="M8.5 8.5l3.5 3.5" stroke="#333" stroke-width="1.8"/></svg>
  </div>
</div>

<div class="catbar">Categories<svg width="12" height="8" viewBox="0 0 12 8"><path d="M1 1l5 5 5-5" fill="none" stroke="#fff" stroke-width="2"/></svg></div>
<div class="crumbs">Computer<i>›</i>Smartphones PDAs &amp; Mobiles</div>

<div class="tab all">All Results (732)</div>
<div class="tab offers">Special Offers</div>

<main class="panel">
  <h1>Smartphones &amp; Mobile Phones</h1>
  <div class="rule"></div>

  <aside class="filters">
    <h2>Thread Count</h2>
    <ul><li>200</li><li>300</li></ul>
    <h2>Bedding Size</h2>
    <ul><li>Single</li><li>Double</li><li>Kingsize</li><li>Super King</li><li>Pillow Case</li></ul>
    <h2>Availability</h2>
    <ul><li>1 Week</li><li>1 Week</li><li>6 Week</li><li>10 Week</li></ul>
    <h2>Colour</h2>
    <ul><li>Blues</li><li>Browns</li><li>Colourful</li><li>Greys</li><li>Metallic</li><li>Neeutrals</li><li>Oak</li><li>Patterned</li><li>Purples</li><li>Turquoise</li><li>Whites</li></ul>
    <h2>Price</h2>
    <ul><li>$0 - $ 250</li><li>$250 - $ 500</li><li>$500 - $ 750</li><li>$750 - $ 1000</li><li>$1000 - $ 1250</li></ul>
  </aside>

  <section class="grid">
    <article class="card"><svg class="ribbon" viewBox="0 0 52 52"><path d="M0 0h52L0 52z" fill="#d6503f"/><text x="13" y="30" transform="rotate(-45 13 30)" font-family="Open Sans,sans-serif" font-size="7" font-weight="700" fill="#fff">FREE</text><text x="10" y="40" transform="rotate(-45 10 40)" font-family="Open Sans,sans-serif" font-size="7" font-weight="700" fill="#fff">DELIVERY</text></svg><div class="shot" role="img" aria-label="Product photo: silver wristwatch with mesh strap"></div><h3>Fontry Double Bed, Oak</h3><ul><li>2.4" Display</li><li>3.5G connectivity</li><li>100-degree panorama camera function</li><li>Nimbra Xpress Browser</li></ul><div class="price">$56.99<small>inc. vat</small></div><div class="btn">VIEW PRODUCT</div></article>
    <article class="card"><svg class="ribbon" viewBox="0 0 52 52"><path d="M0 0h52L0 52z" fill="#d6503f"/><text x="13" y="30" transform="rotate(-45 13 30)" font-family="Open Sans,sans-serif" font-size="7" font-weight="700" fill="#fff">FREE</text><text x="10" y="40" transform="rotate(-45 10 40)" font-family="Open Sans,sans-serif" font-size="7" font-weight="700" fill="#fff">DELIVERY</text></svg><div class="shot" role="img" aria-label="Product photo: silver wristwatch with mesh strap"></div><h3>Fontry Double Bed, Oak</h3><ul><li>2.4" Display</li><li>3.5G connectivity</li><li>100-degree panorama camera function</li><li>Nimbra Xpress Browser</li></ul><div class="price">$56.99<small>inc. vat</small></div><div class="btn">VIEW PRODUCT</div></article>
    <article class="card"><svg class="ribbon" viewBox="0 0 52 52"><path d="M0 0h52L0 52z" fill="#d6503f"/><text x="13" y="30" transform="rotate(-45 13 30)" font-family="Open Sans,sans-serif" font-size="7" font-weight="700" fill="#fff">FREE</text><text x="10" y="40" transform="rotate(-45 10 40)" font-family="Open Sans,sans-serif" font-size="7" font-weight="700" fill="#fff">DELIVERY</text></svg><div class="shot" role="img" aria-label="Product photo: silver wristwatch with mesh strap"></div><h3>Fontry Double Bed, Oak</h3><ul><li>2.4" Display</li><li>3.5G connectivity</li><li>100-degree panorama camera function</li><li>Nimbra Xpress Browser</li></ul><div class="price">$56.99<small>inc. vat</small></div><div class="btn">VIEW PRODUCT</div></article>
    <article class="card"><svg class="ribbon" viewBox="0 0 52 52"><path d="M0 0h52L0 52z" fill="#d6503f"/><text x="13" y="30" transform="rotate(-45 13 30)" font-family="Open Sans,sans-serif" font-size="7" font-weight="700" fill="#fff">FREE</text><text x="10" y="40" transform="rotate(-45 10 40)" font-family="Open Sans,sans-serif" font-size="7" font-weight="700" fill="#fff">DELIVERY</text></svg><div class="shot" role="img" aria-label="Product photo: silver wristwatch with mesh strap"></div><h3>Fontry Double Bed, Oak</h3><ul><li>2.4" Display</li><li>3.5G connectivity</li><li>100-degree panorama camera function</li><li>Nimbra Xpress Browser</li></ul><div class="price">$56.99<small>inc. vat</small></div><div class="btn">VIEW PRODUCT</div></article>
    <article class="card"><svg class="ribbon" viewBox="0 0 52 52"><path d="M0 0h52L0 52z" fill="#d6503f"/><text x="13" y="30" transform="rotate(-45 13 30)" font-family="Open Sans,sans-serif" font-size="7" font-weight="700" fill="#fff">FREE</text><text x="10" y="40" transform="rotate(-45 10 40)" font-family="Open Sans,sans-serif" font-size="7" font-weight="700" fill="#fff">DELIVERY</text></svg><div class="shot" role="img" aria-label="Product photo: silver wristwatch with mesh strap"></div><h3>Fontry Double Bed, Oak</h3><ul><li>2.4" Display</li><li>3.5G connectivity</li><li>100-degree panorama camera function</li><li>Nimbra Xpress Browser</li></ul><div class="price">$56.99<small>inc. vat</small></div><div class="btn">VIEW PRODUCT</div></article>
    <article class="card"><svg class="ribbon" viewBox="0 0 52 52"><path d="M0 0h52L0 52z" fill="#d6503f"/><text x="13" y="30" transform="rotate(-45 13 30)" font-family="Open Sans,sans-serif" font-size="7" font-weight="700" fill="#fff">FREE</text><text x="10" y="40" transform="rotate(-45 10 40)" font-family="Open Sans,sans-serif" font-size="7" font-weight="700" fill="#fff">DELIVERY</text></svg><div class="shot" role="img" aria-label="Product photo: silver wristwatch with mesh strap"></div><h3>Fontry Double Bed, Oak</h3><ul><li>2.4" Display</li><li>3.5G connectivity</li><li>100-degree panorama camera function</li><li>Nimbra Xpress Browser</li></ul><div class="price">$56.99<small>inc. vat</small></div><div class="btn">VIEW PRODUCT</div></article>
    <article class="card"><svg class="ribbon" viewBox="0 0 52 52"><path d="M0 0h52L0 52z" fill="#d6503f"/><text x="13" y="30" transform="rotate(-45 13 30)" font-family="Open Sans,sans-serif" font-size="7" font-weight="700" fill="#fff">FREE</text><text x="10" y="40" transform="rotate(-45 10 40)" font-family="Open Sans,sans-serif" font-size="7" font-weight="700" fill="#fff">DELIVERY</text></svg><div class="shot" role="img" aria-label="Product photo: silver wristwatch with mesh strap"></div><h3>Fontry Double Bed, Oak</h3><ul><li>2.4" Display</li><li>3.5G connectivity</li><li>100-degree panorama camera function</li><li>Nimbra Xpress Browser</li></ul><div class="price">$56.99<small>inc. vat</small></div><div class="btn">VIEW PRODUCT</div></article>
    <article class="card"><svg class="ribbon" viewBox="0 0 52 52"><path d="M0 0h52L0 52z" fill="#d6503f"/><text x="13" y="30" transform="rotate(-45 13 30)" font-family="Open Sans,sans-serif" font-size="7" font-weight="700" fill="#fff">FREE</text><text x="10" y="40" transform="rotate(-45 10 40)" font-family="Open Sans,sans-serif" font-size="7" font-weight="700" fill="#fff">DELIVERY</text></svg><div class="shot" role="img" aria-label="Product photo: silver wristwatch with mesh strap"></div><h3>Fontry Double Bed, Oak</h3><ul><li>2.4" Display</li><li>3.5G connectivity</li><li>100-degree panorama camera function</li><li>Nimbra Xpress Browser</li></ul><div class="price">$56.99<small>inc. vat</small></div><div class="btn">VIEW PRODUCT</div></article>
    <article class="card"><svg class="ribbon" viewBox="0 0 52 52"><path d="M0 0h52L0 52z" fill="#d6503f"/><text x="13" y="30" transform="rotate(-45 13 30)" font-family="Open Sans,sans-serif" font-size="7" font-weight="700" fill="#fff">FREE</text><text x="10" y="40" transform="rotate(-45 10 40)" font-family="Open Sans,sans-serif" font-size="7" font-weight="700" fill="#fff">DELIVERY</text></svg><div class="shot" role="img" aria-label="Product photo: silver wristwatch with mesh strap"></div><h3>Fontry Double Bed, Oak</h3><ul><li>2.4" Display</li><li>3.5G connectivity</li><li>100-degree panorama camera function</li><li>Nimbra Xpress Browser</li></ul><div class="price">$56.99<small>inc. vat</small></div><div class="btn">VIEW PRODUCT</div></article>
    <article class="card"><svg class="ribbon" viewBox="0 0 52 52"><path d="M0 0h52L0 52z" fill="#d6503f"/><text x="13" y="30" transform="rotate(-45 13 30)" font-family="Open Sans,sans-serif" font-size="7" font-weight="700" fill="#fff">FREE</text><text x="10" y="40" transform="rotate(-45 10 40)" font-family="Open Sans,sans-serif" font-size="7" font-weight="700" fill="#fff">DELIVERY</text></svg><div class="shot" role="img" aria-label="Product photo: silver wristwatch with mesh strap"></div><h3>Fontry Double Bed, Oak</h3><ul><li>2.4" Display</li><li>3.5G connectivity</li><li>100-degree panorama camera function</li><li>Nimbra Xpress Browser</li></ul><div class="price">$56.99<small>inc. vat</small></div><div class="btn">VIEW PRODUCT</div></article>
  </section>
</main>

<footer class="footer">
  <div class="fcol" style="left:183px">
    <h4>Contact Us</h4>
    <p><svg width="10" height="12" viewBox="0 0 10 12"><path d="M5 0a4 4 0 0 0-4 4c0 3 4 8 4 8s4-5 4-8a4 4 0 0 0-4-4z" fill="#fff"/><circle cx="5" cy="4" r="1.5" fill="#3a3d42"/></svg>12 Fernway, 40 Dunmore</p>
    <p><svg width="11" height="11" viewBox="0 0 14 14"><path d="M3 1h3l1 3-2 1a8 8 0 0 0 4 4l1-2 3 1v3c0 1-1 2-2 2A11 11 0 0 1 1 3c0-1 1-2 2-2z" fill="#fff"/></svg>+000 (000) 0000</p>
    <p><svg width="11" height="8" viewBox="0 0 11 8"><rect width="11" height="8" fill="#fff"/><path d="M0 0l5.5 4.5L11 0" fill="none" stroke="#3a3d42"/></svg>mail@example.com</p>
  </div>
  <div class="fcol" style="left:397px">
    <h4>Information</h4>
    <p>About Us</p><p>Privacy Policy</p><p>Terms &amp; Conditions</p><p>Secure Payment</p>
  </div>
  <div class="fcol" style="left:613px">
    <h4>Costumer Service</h4>
    <p>Contact Us</p><p>Return</p><p>FAQ</p><p>Site Map</p>
  </div>
  <div class="fcol" style="left:829px">
    <h4>My Account</h4>
    <p>My Account</p><p>Order History</p><p>Wish List</p><p>Newsletter</p>
  </div>
</footer>

<div class="bottom">
  <div class="copy">© 2014 Lumavorp. All rights reserved.</div>
  <div class="social"><span>plaztrove</span><span>Chirpwell</span><span>Orbiq</span></div>
</div>
</body>
</html>
```